Corvane Paintless Dent Removal

Our company works on vehicles removing dents using a highly skilled trade which the metal is massaged out with special tools without disturbing the original paint, hence paintless dent removal. Besides keeping the paint and metal original its also very environmentally friendly since no paint or toxic fillers are used. Also we we are one of the most experienced companies in the business with 25 years

Target Market(s)

Retail Automobile consumers, Auto Dealerships and Auto Body Shops

Industry/Entity Type

Auto Repair

Contact Information for Business Card

Dale Hollister
PO Box 518 Brookmere, NY 11962
631-555-0148
corvanepdr@mailbox-example.com
website corvanepdr.example
youtube corvane paintless dent removal
25 years of experience removing Dents, Dings and Hail Damage

Font styles to use
Serif
Sans Serif

Colors

Designer to choose colors to be used in the design.

Requirements
Must have
• I do like things that are simple but classy and somewhat bold, also I like my logo so that should be somewhat important

```html
<!DOCTYPE html>
<html lang="en">
<head>
<meta charset="utf-8">
<title>Corvane Paintless Dent Removal – Business Card</title>
<link href="https://fonts.googleapis.com/css2?family=Roboto:wght@400;500;700;900&family=Roboto+Condensed:wght@500;700&display=swap" rel="stylesheet">
<style>
  :root {
    --navy: #13294f;
    --green: #7cc21f;
    --gold: #c99a2e;
    --paper: #f4f4f4;
    --ink: #3e3e3e;
    --backdrop: #e6e4e1;
    --white: #ffffff;
  }
  * { margin: 0; padding: 0; box-sizing: border-box; }
  html, body { width: 1200px; height: 960px; overflow: hidden; }
  body { background: var(--backdrop); font-family: "Roboto", Arial, sans-serif; position: relative; }

  .card { position: absolute; width: 600px; height: 342px; overflow: hidden; box-shadow: 0 3px 8px rgba(0,0,0,.25); }
  .card--front { left: 314px; top: 113px; background: var(--paper); }
  .card--back { left: 311px; top: 472px; background: var(--navy); }

  .brand { position: absolute; left: 40px; top: 150px; width: 250px; text-align: center; color: var(--navy); font-weight: 900; line-height: 1; }
  .brand__name { display: block; font-size: 34px; letter-spacing: .5px; }
  .brand__trade { display: block; font-size: 13px; margin-top: 4px; }

  .divider { position: absolute; left: 307px; top: 112px; width: 2px; height: 155px; background: linear-gradient(to bottom, transparent, #c9c9c9 20%, #c9c9c9 80%, transparent); }

  .seal { position: absolute; left: 505px; top: 33px; width: 70px; height: 70px; border-radius: 50%; background: #1a1a1a; border: 4px solid var(--gold); }

  .contact { position: absolute; left: 332px; top: 110px; color: var(--ink); }
  .contact__name { font-family: "Roboto Condensed", Arial, sans-serif; font-weight: 700; font-size: 21px; color: var(--navy); margin-bottom: 10px; letter-spacing: .2px; }
  .contact__address { font-size: 14px; line-height: 19px; margin-bottom: 8px; color: #555; }
  .contact__list { list-style: none; font-size: 14px; line-height: 19px; }
  .contact__list li { display: flex; align-items: center; gap: 8px; }
  .contact__list svg { width: 14px; height: 14px; flex: none; fill: var(--navy); }

  .band { position: absolute; left: 0; bottom: 0; width: 600px; height: 32px; }
  .band__url { position: absolute; right: 24px; bottom: 7px; color: var(--white); font-size: 13px; letter-spacing: 2.4px; }

  .back-brand { position: absolute; left: 41px; top: 243px; color: var(--white); font-weight: 900; line-height: 1; }
  .back-brand__name { display: block; font-size: 40px; letter-spacing: -.5px; }
  .back-brand__trade { display: block; font-size: 16px; margin-top: 2px; }
  .back-brand__url { display: block; font-weight: 400; font-size: 13px; letter-spacing: 2.6px; margin-top: 4px; }
</style>
</head>
<body>

<section class="card card--front" aria-label="Business card front">
  <div class="brand">
    <span class="brand__name">CORVANE</span>
    <span class="brand__trade">Paintless Dent Removal</span>
  </div>

  <div class="divider"></div>
  <div class="seal" role="img" aria-label="25 years of experience seal"></div>

  <div class="contact">
    <h1 class="contact__name">DALE HOLLISTER</h1>
    <p class="contact__address">PO Box 518<br>Brookmere, NY 11962</p>
    <ul class="contact__list">
      <li><svg viewBox="0 0 24 24" aria-hidden="true"><path d="M6.6 10.8a15.1 15.1 0 0 0 6.6 6.6l2.2-2.2c.3-.3.7-.4 1-.2 1.1.4 2.3.6 3.6.6.6 0 1 .4 1 1V20c0 .6-.4 1-1 1A17 17 0 0 1 3 4c0-.6.4-1 1-1h3.5c.6 0 1 .4 1 1 0 1.3.2 2.5.6 3.6.1.3 0 .7-.2 1z"/></svg>631-555-0148</li>
      <li><svg viewBox="0 0 24 24" aria-hidden="true"><path d="M2 5h20v14H2z M4 7v1l8 5 8-5V7l-8 5z" fill-rule="evenodd"/></svg>corvanepdr@mailbox-example.com</li>
      <li><svg viewBox="0 0 24 24" aria-hidden="true"><rect x="3" y="5" width="18" height="14" rx="2"/></svg>corvane paintless dent removal</li>
    </ul>
  </div>

  <svg class="band" viewBox="0 0 600 32" preserveAspectRatio="none" aria-hidden="true">
    <path d="M0 14 H320 Q330 14 333 20 L334 22 H0 Z" fill="var(--green)"/>
    <path d="M0 22 H332 Q336 32 345 32 H0 Z" fill="#d9d9d9"/>
    <path d="M600 0 H350 Q338 0 335 10 L328 32 H600 Z" fill="var(--navy)"/>
  </svg>
  <span class="band__url">www.corvanepdr.example</span>
</section>

<section class="card card--back" aria-label="Business card back">
  <div class="back-brand">
    <span class="back-brand__name">CORVANE</span>
    <span class="back-brand__trade">Paintless Dent Removal</span>
    <span class="back-brand__url">www.corvanepdr.example</span>
  </div>
</section>

</body>
</html>
```